$5 Quest Website Required

I am looking for someone to develop a website akin to the simplicity of www.boxlantern.example with a video in the center or a tab that permits one to "Accept the Challenge."

Incorporates our logo and is used to promote our "$5 Quest Program."

Please see attachments, but we are igniting entrepreneurial spirit among our nation's youth through this interactive and intensive program!

There should be a way to navigate to other sections of the site including:

About
Why
Request $5 Quest Packet
Success Stories
Partners
Link to Norvik Holdings
Updates

Thanks to all in advance!

Looking forward to working with you!

Good feel of what we are looking for in terms of "feel"

http://www.thebrightripple.example/

Thank you,

RB

Please make note of this website, we are going for a feel that is akin to this and less modern and professional...more abstract and interactive...but of course include space for our video:

Colors, feel, imagery, is great. Keep your formats, but bring on the feel!

Thank you all for your hard work and patience.

Thank you all for your hard work thus far.

Meanwhile, please understand that the $5 Quest is young, youthful, full of challenge and vitality, it is a competition among students from high school and universities.  The websites you have delivered are too corporate, stale, and standard.  I'm looking for something that is fresh, different, like www.thebrightripple.example.

Symbols, cartoonish, but serious, down to business and save the world one $5 bill at a time.  The logo can be used as a theme...the colors, the feel.

Video space for explanation on the $5 Quest front and center.  With leaves, $ signs, colorful colors, etc.

Visual needs to be compelling to Join the Challenge! Although Norvik Holdings and the tree is a parent company; $5 Quest is separate and Norvik Holdings should only be mentioned as a link.

PixelHarbor.example in regard to simplicity; and www.thebrightripple.example in terms of style.

Thank you,

Raphael

Like the designs that have been submitted; we are almost there.

Target Market(s)

Professors, students, teachers, parents and NGO leaders who wish to use our program as a way to inspire leadership/entrepreneurship/fundraise for their causes.

Requirements
Must have
• Place for the video, front and center
Include logo
Forsight for blogging, message, etc.
Nice to have
• Plan "buckets" to include"
Explanation Video
Two pamphlets
Contract
FAQs
Website with Blog, voting, registration, video upload, etc.
Flyer perfected
Parable...symbol of our life
Photos
Stats included
Testimonials
Organizations that have used (TKWLM, North Brook Lodge, Marlowton High)
Sponsors (Open Lantern, Copperleaf Learningfield)
Photos from events

I understand this takes coding and such, but want you to be aware of the long term vision for it!

```html
<!DOCTYPE html>
<html lang="en">
<head>
<meta charset="utf-8">
<title>$5 Quest</title>
<link rel="stylesheet" href="https://fonts.googleapis.com/css2?family=Roboto+Condensed:wght@400;700&family=Arimo:wght@400&display=swap">
<style>
  :root {
    --leaf-dark: #0d8a3c;
    --leaf-mid: #3dbb4e;
    --leaf-lime: #cfe03a;
    --orange: #fea800;
    --ribbon: #0b8d3b;
    --ribbon-edge: #076a2b;
    --home: #e9e63c;
    --ink: #333333;
    --logo-grey: #555555;
    --button-lime: #d6e43c;
    --button-edge: #b9c92a;
    --white: #ffffff;
  }
  * { margin: 0; padding: 0; box-sizing: border-box; }
  html, body { width: 1063px; height: 1200px; overflow: hidden; background: var(--white); }
  .stage { position: relative; width: 1063px; height: 1200px; font-family: "Arimo", Arial, sans-serif; }
  .stage-art { position: absolute; inset: 0; }
  .top-links { position: absolute; top: 131px; left: 705px; display: flex; align-items: center; gap: 16px;
    font-family: "Roboto Condensed", sans-serif; font-weight: 700; font-size: 14px; color: #222; letter-spacing: .5px; white-space: nowrap; }
  .language { background: var(--orange); color: #111; font-size: 12px; padding: 5px 9px; border: 1px solid #e59500; white-space: nowrap; }
  .brand { position: absolute; top: 204px; left: 0; width: 1063px; display: flex; justify-content: center; align-items: center; gap: 14px; }
  .brand-dot { width: 62px; height: 62px; border-radius: 50%; background: var(--leaf-mid); }
  .brand-name { font-family: "Arimo", Arial, sans-serif; font-size: 74px; color: var(--logo-grey); }
  .main-nav { position: absolute; top: 330px; left: 0; width: 1063px; display: flex; justify-content: center; gap: 21px;
    font-family: "Roboto Condensed", sans-serif; font-weight: 700; font-size: 19px; color: var(--white); white-space: nowrap; }
  .main-nav .current { color: var(--home); }
  .welcome { position: absolute; top: 392px; left: 0; width: 1063px; text-align: center;
    font-family: "Roboto Condensed", sans-serif; font-weight: 400; font-size: 21px; color: var(--white); }
  .intro { position: absolute; top: 430px; left: 202px; width: 666px; font-size: 12.9px; line-height: 19px; color: var(--ink); }
  .watch-label { position: absolute; top: 690px; left: 0; width: 1063px; text-align: center;
    font-family: "Roboto Condensed", sans-serif; font-size: 22px; color: #222; }
  .accept { position: absolute; top: 838px; left: 0; width: 1063px; text-align: center;
    font-family: "Roboto Condensed", sans-serif; font-size: 22px; color: #333; }
  .foot-brand { position: absolute; top: 948px; left: 0; width: 1063px; text-align: center; font-size: 24px; color: var(--leaf-dark); }
  .copyright { position: absolute; top: 1003px; left: 0; width: 1063px; text-align: center; font-size: 12px; color: var(--ink); }
</style>
</head>
<body>
<div class="stage">
  <svg class="stage-art" width="1063" height="1200" viewBox="0 0 1063 1200">
    <defs>
      <radialGradient id="leafRing" cx="50%" cy="50%" r="50%">
        <stop offset="0.66" stop-color="#ffffff" stop-opacity="0"/>
        <stop offset="0.72" stop-color="#0d8a3c" stop-opacity=".85"/>
        <stop offset="0.84" stop-color="#3dbb4e" stop-opacity=".75"/>
        <stop offset="0.95" stop-color="#cfe03a" stop-opacity=".6"/>
        <stop offset="1" stop-color="#cfe03a" stop-opacity="0"/>
      </radialGradient>
      <clipPath id="oval"><ellipse cx="532" cy="588" rx="368" ry="461"/></clipPath>
      <filter id="soft" x="-20%" y="-20%" width="140%" height="140%"><feGaussianBlur stdDeviation="6"/></filter>
    </defs>

    <ellipse cx="532" cy="596" rx="520" ry="594" fill="url(#leafRing)" role="img" aria-label="Ring of green and lime leaves surrounding the page"/>

    <ellipse cx="532" cy="592" rx="370" ry="463" fill="#000" opacity=".25" filter="url(#soft)"/>
    <ellipse cx="532" cy="588" rx="368" ry="461" fill="var(--white)"/>

    <g clip-path="url(#oval)">
      <rect x="150" y="372" width="770" height="552" fill="var(--orange)" role="img" aria-label="Faint background illustration of the quest steps on orange"/>
      <line x1="226" y1="852" x2="844" y2="852" stroke="#222" stroke-width="1.5" stroke-dasharray="5 4"/>
    </g>

    <polygon points="129,319 165,319 165,372 129,372 147,345" fill="var(--ribbon-edge)"/>
    <polygon points="934,319 898,319 898,372 934,372 916,345" fill="var(--ribbon-edge)"/>
    <rect x="153" y="321" width="757" height="49" fill="var(--ribbon)"/>

    <rect x="354" y="487" width="360" height="296" rx="4" fill="#000" opacity=".2" filter="url(#soft)"/>
    <rect x="350" y="481" width="362" height="302" rx="4" fill="var(--white)"/>
    <rect x="358" y="489" width="346" height="286" fill="#f4f4f4" stroke="#d6d6d6" stroke-width="2"/>
    <circle cx="530" cy="607" r="60" fill="#222"/>
    <polygon points="518,583 518,631 551,607" fill="#bdbdbd"/>

    <polygon points="356,827 702,827 690,853 702,880 356,880 368,853" fill="var(--button-lime)" stroke="var(--button-edge)" stroke-width="3"/>
  </svg>

  <nav class="top-links"><span>FAQ</span><span>SIGNIN</span><span class="language">LANGUAGE ▼</span></nav>

  <div class="brand"><span class="brand-dot"></span><span class="brand-name">$5 Quest</span></div>

  <nav class="main-nav">
    <span class="current">HOME</span><span>ABOUT US</span><span>WHY WE ARE?</span><span>SUCCESS STORIES</span><span>PARTNERS</span><span>NORVIK HOLDINGS</span>
  </nav>

  <h1 class="welcome">WELCOME TO $5 QUEST</h1>
  <p class="intro">Lorem ipsum dolor sit amet, consectetur adipiscing elit. Curabitur eu nisl odio. Cras egestas turpis in mi feugiat vel tincidunt arcu accumsan. Phasellus non posuere eros. Aenean consectetur.</p>

  <div class="watch-label">WATCH VIDEO</div>
  <div class="accept">ACCEPT THE CHALLENGE</div>

  <div class="foot-brand">$5 Quest</div>
  <p class="copyright">All Rights reserved @ $5quest</p>
</div>
</body>
</html>
```